Communication and Marketing agency needs a new presentation card

We are a group of communication and marketing agencies specialized in companies that are in the logistics and industrial sector. The head agency is TELVANO Grupo and the group consists of 4 agencies: TELVANO Media, TELVANO Digital, TELVANO Research and DifundeEnPantalla. We hace 4 offices in Spain (Madrid, Barcelona, Valencia and Murcia). We are looking for a clean and attractive design that transmits our experience, brand presence in the market and knowledge to those who receive the card.It has to maintain the colors of the logo that is attached.
Target Market(s)
logistics and industrial sector
Marketing department
Contact Information for Business Card
Clean and attractive design

```html
<!DOCTYPE html>
<html lang="es">
<head>
<meta charset="utf-8">
<title>TELVANO Grupo – Tarjeta de presentación</title>
<link rel="stylesheet" href="https://fonts.googleapis.com/css2?family=Roboto:wght@300;400;500;700&display=swap">
<style>
  :root {
    --stage: #e6e4e1;
    --card-dark: #2e2c2c;
    --card-dark-edge: #3b3939;
    --panel: #ffffff;
    --brand-red: #b3132a;
    --ink-grey: #5a5a5a;
    --rule: #c9c9c9;
    --icon-dark: #3a3838;
  }
  * { box-sizing: border-box; margin: 0; padding: 0; }
  html, body {
    width: 1200px;
    height: 900px;
    overflow: hidden;
  }
  body {
    background: var(--stage);
    font-family: "Roboto", Arial, sans-serif;
    position: relative;
  }
  .card {
    position: absolute;
    top: 282px;
    width: 520px;
    height: 336px;
    background: linear-gradient(135deg, var(--card-dark-edge) 0%, var(--card-dark) 55%, #262424 100%);
    box-shadow: 0 14px 34px rgba(0, 0, 0, 0.28);
    overflow: hidden;
  }
  .card--front { left: 60px; }
  .card--back  { left: 620px; }

  .card__panel {
    position: absolute;
    top: 0;
    height: 100%;
    background: var(--panel);
  }
  .card--front .card__panel {
    left: 112px;
    width: 236px;
    padding: 36px 22px 0 24px;
  }
  .card--back .card__panel {
    left: 272px;
    width: 248px;
    display: flex;
    align-items: center;
    justify-content: center;
  }

  .contact__name {
    font-size: 21px;
    font-weight: 500;
    color: var(--brand-red);
    letter-spacing: 0.1px;
  }
  .contact__role {
    font-size: 18px;
    font-weight: 300;
    color: var(--ink-grey);
    margin-top: 2px;
  }
  .contact__rule {
    border: none;
    border-top: 1px solid var(--rule);
    margin: 14px 0 14px;
  }
  .contact__lines {
    list-style: none;
    font-size: 15px;
    font-weight: 300;
    color: var(--ink-grey);
    line-height: 21px;
  }
  .contact__social {
    display: flex;
    align-items: center;
    gap: 6px;
  }
  .contact__social-dot {
    width: 13px;
    height: 13px;
    border-radius: 50%;
    background: var(--icon-dark);
    flex: none;
  }
  .contact__web {
    margin-top: 14px;
    font-size: 17px;
    font-weight: 400;
    color: var(--brand-red);
  }

  .brand-name {
    font-size: 34px;
    font-weight: 400;
    color: var(--brand-red);
    letter-spacing: 1px;
    text-align: center;
    line-height: 1.1;
  }
  .brand-name span { display: block; font-size: 22px; letter-spacing: 0.5px; }
</style>
</head>
<body>

  <section class="card card--front" aria-label="Anverso de la tarjeta">
    <div class="card__panel">
      <h1 class="contact__name">Adrián Quesada</h1>
      <p class="contact__role">Director</p>
      <hr class="contact__rule">
      <ul class="contact__lines">
        <li>T. 914 527 310</li>
        <li>M. 655 208 417</li>
        <li>aquesada@telvano.es</li>
        <li class="contact__social"><span class="contact__social-dot"></span>adrianquesada</li>
      </ul>
      <p class="contact__web">www.telvano.es</p>
    </div>
  </section>

  <section class="card card--back" aria-label="Reverso de la tarjeta">
    <div class="card__panel">
      <p class="brand-name">TELVANO <span>Grupo</span></p>
    </div>
  </section>

</body>
</html>
```